Website Redesign for Non-Profit Ministry & Church

NOTE: Please do not contact me privately — all private inquiries will be ignored.

Individuals seeking spiritual healing, community connection, ministry support and journal-based encounters.

Description of What’s Needed

We need a clean, fresh, inviting website that encourages engagement and connection. The site should feel warm and accessible, draw people in, and clearly present who we are, what we offer, and how visitors can participate. The layout should be straightforward, with well-structured pages (no overlapping objects, minimal layering complexity) and easy to navigate. Use only Google Fonts. All stock photos must be sourced from royalty-free sites and include proper attribution. We will not include a search feature.

Pages to Create
1. Home Page – impactful hero area, clear call-to-action, visual story of ministry, giving/gathering invitation.
2. About Us – vision, mission, leadership, testimonies, history.
3. Meetings & Events – upcoming gatherings, schedule, how to attend, sign-up or interest form.
4. Encounter: “Lanterns by the River” (book) – dedicated page for the book, overview, purchase link or details, journal prompts, imagery.
5. Healing Rooms / Ministry – explain ministry offerings, invite participation, testimonials or case-studies.
6. Live Stream & Links Page – page listing links for YouTube live stream, other platforms, archive links; simple layout.

Colour & Branding

Use colours that blend with our existing logo (attached). The palette should feel contemporary, welcoming, and aligned with ministry themes of restoration, healing and love. Ensure text, button and link colours maintain good contrast for accessibility.

Existing Content & Reference

Please gather available content from our current website in the attachment here for text, images and structure for reuse.

Imagery Guidelines

– Use original photos from our Facebook page or Google Location listing for building or people images when available.
– If generic images are used, ensure they depict appropriate ministry-related buildings or people (community, warm gathering) — avoid generic unrelated stock imagery.
– All photos must be royalty-free or have proper licensing and attribution.
– No overlapping objects or visual clutter; clean layouts with defined sections.

Additional Notes

– Integration: We currently utilise MailChimp for email communication; the design should include a connection/invite to subscribe (via MailChimp) but no blog page is required at this time.
– Payment/Giving: We accept PayPal and already have a giving portal; include clear donation/give buttons or calls-to-action linking to existing giving systems.
– No search function to be included.
– Layouts should avoid complex layering or overlapping elements—designers should work with distinct content blocks, clear visual hierarchy, and straightforward mobile-friendly structure.

Target Market(s)

Industry/Entity Type

Church/Religious institution

Number of Pages Required

5+ page

Requirements
Should not have
• search bar

```html
<!DOCTYPE html>
<html lang="en">
<head>
<meta charset="utf-8">
<title>Mended Held Whole — Home</title>
<link href="https://fonts.googleapis.com/css2?family=Outfit:wght@400;500;600;700&display=swap" rel="stylesheet">
<style>
:root{
  --teal:#13a597;
  --green:#0c6b4a;
  --purple:#6a2b93;
  --purple-band:#5f2a8d;
  --ink:#222;
  --white:#fff;
  --mint:#a9e3dc;
  --line:#bdbdbd;
}
*{box-sizing:border-box;margin:0;padding:0}
html,body{width:1200px;height:3058px;overflow:hidden}
body{position:relative;font-family:"Outfit",sans-serif;color:var(--ink);background:var(--white)}
.abs{position:absolute}
.brand{display:flex;align-items:center;gap:10px;font-weight:700;color:var(--teal);line-height:1}
.brand-dot{width:30px;height:30px;border-radius:50%;border:3px solid var(--teal)}
.site-brand{left:0;width:1200px;top:28px;justify-content:center;font-size:26px}
.nav{left:125px;top:100px;width:950px;height:51px;background:var(--white);border-radius:26px;
  box-shadow:0 2px 8px rgba(0,0,0,.08);display:flex;justify-content:space-between;align-items:center;
  padding:0 38px;font-size:14px;font-weight:500;z-index:2}
.nav a{color:var(--ink);text-decoration:none}
.nav a.current{color:var(--purple)}
.hero-photo{left:0;top:125px;width:1200px;height:514px;
  background:linear-gradient(180deg,#d8d2cb 0%,#c9bfb4 45%,#4a3a7a 75%,#3b2d6a 100%)}
.hero-card{left:826px;top:360px;width:322px;height:217px;background:var(--white);border-radius:28px;
  display:flex;flex-direction:column;align-items:center;justify-content:center;gap:14px;text-align:center}
.mark{width:26px;height:26px;border-radius:50%;border:3px solid var(--teal);flex:none}
.hero-title{font-size:31px;font-weight:700;line-height:1.5;letter-spacing:-.3px}
.c-green{color:var(--green)}.c-purple{color:var(--purple)}.c-teal{color:var(--teal)}
.church-back{left:124px;top:734px;width:398px;height:500px;background:var(--mint);border-radius:70px 40px 60px 40px}
.church-photo{left:110px;top:722px;width:405px;height:502px;border-radius:70px 50px 60px 60px;
  background:linear-gradient(180deg,#5d74b3 0%,#8d9bc8 30%,#a65a43 55%,#7c4030 80%,#2e2a26 100%)}
.section-head{display:flex;align-items:center;gap:14px;font-size:31px;font-weight:700;letter-spacing:-.3px}
.mission-head{left:584px;top:744px}
.copy{font-size:16.5px;line-height:37px}
.mission-copy{left:584px;top:806px;width:520px}
.sub-head{left:584px;top:976px;font-size:25px;font-weight:600;color:var(--green)}
.story-copy{left:584px;top:1022px;width:520px}
.btn{display:flex;align-items:center;justify-content:center;font-size:15.5px;font-weight:500;border-radius:5px;text-decoration:none}
.btn-fill{background:var(--teal);color:var(--white)}
.btn-line{border:1.5px solid var(--teal);color:var(--teal);background:var(--white)}
.learn-1{left:584px;top:1169px;width:144px;height:43px}
.invite{left:747px;top:1169px;width:102px;height:43px}
.band{left:0;top:1321px;width:1200px;height:578px;background:var(--purple-band)}
.book-head{left:110px;top:1393px;align-items:flex-start;color:var(--white);line-height:48px}
.book-head .mark{margin-top:12px}
.book-copy{left:110px;top:1506px;width:500px;color:var(--white)}
.book-copy p+p{margin-top:15px}
.book-now{left:110px;top:1777px;width:144px;height:42px}
.book-cover{left:683px;top:1385px;width:359px;height:450px;border-radius:60px 50px 70px 70px;
  background:linear-gradient(160deg,#0b1a14 0%,#1f4a2c 45%,#3a6a30 65%,#0d1410 100%)}
.who-head{left:0;width:1200px;top:1970px;justify-content:center}
.who-copy{left:125px;top:2040px;width:950px;text-align:center}
.learn-2{left:528px;top:2259px;width:144px;height:42px}
.foot-band{left:0;top:2522px;width:1200px;height:536px;background:var(--purple-band)}
.news-card{left:112px;top:2382px;width:976px;height:272px;background:var(--white);border-radius:30px;box-shadow:0 2px 10px rgba(0,0,0,.06)}
.news-head{left:0;width:1200px;top:2418px;justify-content:center;font-size:28px}
.news-copy{left:0;width:1200px;top:2480px;text-align:center;font-size:16px}
.field{top:2556px;height:46px;width:221px;border:1px solid var(--line);border-radius:3px;
  display:flex;align-items:center;padding-left:16px;font-size:13px;color:#555;background:var(--white)}
.f1{left:159px}.f2{left:405px}.f3{left:650px}
.subscribe{left:896px;top:2556px;width:144px;height:46px;font-size:16px}
.foot-brand{left:102px;top:2735px;font-size:30px;color:var(--white)}
.foot-brand .brand-dot{border-color:var(--white);width:40px;height:40px}
.social{top:2845px;width:31px;height:31px;border:1.5px solid rgba(255,255,255,.8);border-radius:6px}
.s1{left:170px}.s2{left:218px}
.foot-col{top:2712px;color:var(--white)}
.foot-col h4{font-size:19px;font-weight:500;color:var(--teal);margin-bottom:14px}
.foot-col li{list-style:none;font-size:13px;font-weight:500;line-height:35px;text-transform:uppercase}
.col-links{left:453px}.col-posts{left:793px}
.foot-rule{left:95px;top:2989px;width:1010px;height:1px;background:rgba(255,255,255,.25)}
.copyright{left:0;width:1200px;top:3015px;text-align:center;color:var(--white);font-size:14px;font-weight:500}
</style>
</head>
<body>

<header>
  <div class="abs brand site-brand"><span class="brand-dot"></span>Mended Held Whole</div>
  <nav class="abs nav">
    <a class="current" href="#">HOME</a>
    <a href="#">ABOUT US</a>
    <a href="#">MEETINGS &amp; EVENTS</a>
    <a href="#">ENCOUNTER</a>
    <a href="#">HEALING ROOMS / MINISTRY</a>
    <a href="#">LIVE STREAM &amp; LINKS</a>
  </nav>
</header>

<section>
  <div class="abs hero-photo" role="img" aria-label="A speaker with a microphone addressing a seated congregation in a bright church hall"></div>
  <div class="abs hero-card">
    <span class="mark"></span>
    <h1 class="hero-title"><span class="c-green">MENDED,</span> <span class="c-purple">HELD,</span><br><span class="c-teal">WHOLE</span></h1>
  </div>
</section>

<section>
  <div class="abs church-back"></div>
  <div class="abs church-photo" role="img" aria-label="Brick church building with a round window and entrance stairs at dusk"></div>
  <h2 class="abs section-head mission-head"><span class="mark"></span><span><span class="c-green">OUR</span> <span class="c-purple">MISSION</span> <span class="c-teal">&amp; VISION</span></span></h2>
  <p class="abs copy mission-copy">Honoring God’s presence by loving the broken, saving the lost, and healing the hurting through the demonstration of His love and power. Mended Held Whole is here to activate, proclaim and teach the love of the Father through Jesus with the guidance of the Holy Spirit.</p>
  <h3 class="abs sub-head">STORY OF MINISTRY</h3>
  <p class="abs copy story-copy">Our ministry exists to help people encounter God through worship, prayer, and authentic connection. We believe in healing, compassion, discipleship, and the transformative love of Jesus.</p>
  <a class="abs btn btn-fill learn-1" href="#">LEARN MORE</a>
  <a class="abs btn btn-line invite" href="#">INVITE</a>
</section>

<section>
  <div class="abs band"></div>
  <h2 class="abs section-head book-head"><span class="mark"></span><span>ENCOUNTER: LANTERNS BY<br><span class="c-teal">THE RIVER</span></span></h2>
  <div class="abs copy book-copy">
    <p>Encounter: Lanterns by the River begins with the astounding story of Clara’s journey through difficult times, including many years of suffering from Bipolar Disorder to a healing encounter with Jesus.</p>
    <p>The book is a six-week guided journal with a short daily devotion. The first week examines the “I am” statements of Jesus found in the Gospel of John.</p>
  </div>
  <a class="abs btn btn-fill book-now" href="#">BOOK NOW</a>
  <div class="abs book-cover" role="img" aria-label="Book cover for Encounter: Lanterns by the River by Clara Jean Holloway, yellow flowers in rain on dark foliage"></div>
</section>

<section>
  <h2 class="abs section-head who-head"><span class="mark"></span><span><span class="c-green">WHO</span> <span class="c-purple">WE</span> <span class="c-teal">ARE</span></span></h2>
  <p class="abs copy who-copy">Daniel and Clara Jean have been married for 42 years and have two adult children. They both grew up in southern Ohio. Their desire is to share the love of Christ with others. They have numerous stories to share about the many ways they have seen God move in their lives as well as the lives of others. They believe in the manifestation of God’s power through signs and wonders. They have not only witnessed God’s power through signs and wonders them they have also experienced His miraculous healing touch personally.</p>
  <a class="abs btn btn-fill learn-2" href="#">LEARN MORE</a>
</section>

<footer>
  <div class="abs foot-band"></div>
  <div class="abs news-card"></div>
  <h2 class="abs section-head news-head"><span class="mark"></span><span><span class="c-green">JOIN</span> <span class="c-purple">OUR</span> <span class="c-teal">NEWSLETTER</span></span></h2>
  <p class="abs news-copy">Signup today for free and be the first to get notified on new updates.</p>
  <div class="abs field f1">ENTER YOUR EMAIL</div>
  <div class="abs field f2">ENTER FIRST NAME</div>
  <div class="abs field f3">ENTER LAST NAME</div>
  <a class="abs btn btn-fill subscribe" href="#">SUBSCRIBE</a>

  <div class="abs brand foot-brand"><span class="brand-dot"></span>Mended Held Whole</div>
  <a class="abs social s1" href="#" aria-label="Social profile"></a>
  <a class="abs social s2" href="#" aria-label="Social profile"></a>

  <div class="abs foot-col col-links">
    <h4>QUICK LINKS</h4>
    <ul>
      <li>Home</li><li>About Us</li><li>Meetings &amp; Events</li><li>Encounter</li><li>Healing Rooms / Ministry</li><li>Live Stream &amp; Links</li>
    </ul>
  </div>
  <div class="abs foot-col col-posts">
    <h4>RECENT POSTS</h4>
    <ul>
      <li>Nothing is incurable for God</li><li>Healing amidst the car accident</li><li>Healing – where and how can it happen?</li><li>Why is healing important?</li><li>Now is the time to move!</li>
    </ul>
  </div>
  <div class="abs foot-rule"></div>
  <p class="abs copyright">COPYRIGHT © 2025. ALL RIGHTS RESERVED.</p>
</footer>

</body>
</html>
```